Dalvick's Business Card

I need some designs for a new business card including the new logo attached. An old example of our business card is also attached to show all the data that should be included on the new design.
**I added some more examples someone had mocked up**

Contact Information for Business Card

Should include all info on other examples uploaded.

```html
<!DOCTYPE html>
<html lang="en">
<head>
<meta charset="utf-8">
<title>Dalvick's Business Card</title>
<link href="https://fonts.googleapis.com/css2?family=Lexend:wght@400;500;600;700&display=swap" rel="stylesheet">
<style>
  :root {
    --page: #e4e4e4;
    --card-light: #f7f7f7;
    --card-dark: #ececec;
    --blue: #0b6cb3;
    --red: #d4161d;
    --white: #ffffff;
  }
  * { margin: 0; padding: 0; box-sizing: border-box; }
  html, body { width: 1200px; height: 1200px; overflow: hidden; }
  body {
    background: var(--page);
    font-family: "Lexend", Arial, sans-serif;
    position: relative;
  }
  .card {
    position: absolute;
    left: 150px;
    width: 900px;
    height: 511px;
    background: linear-gradient(120deg, var(--card-light) 0%, var(--card-dark) 60%, var(--card-light) 100%);
    overflow: hidden;
  }
  .card-front { top: 50px; }
  .card-back { top: 621px; }

  .line { position: absolute; font-weight: 500; text-transform: uppercase; letter-spacing: 0.3px; white-space: nowrap; }
  .blue { color: var(--blue); }
  .red { color: var(--red); }

  .service-area { left: 237px; top: 76px; font-size: 19px; line-height: 28px; }

  .brand-mark { position: absolute; width: 26px; height: 26px; border-radius: 50%; background: var(--red); }
  .brand-name { position: absolute; font-weight: 500; color: var(--blue); white-space: nowrap; }

  .front-mark { left: 180px; top: 240px; width: 38px; height: 38px; }
  .front-name { left: 233px; top: 192px; font-size: 92px; line-height: 110px; letter-spacing: 1px; }
  .tagline { left: 237px; top: 286px; font-size: 21px; }

  .call-out { left: 237px; top: 382px; font-size: 19px; line-height: 29px; }

  .back-mark { left: 120px; top: 206px; }
  .back-name { left: 156px; top: 194px; font-size: 40px; line-height: 48px; }

  .person-name { position: absolute; left: 426px; top: 125px; font-size: 37px; font-weight: 700; color: var(--red); }
  .divider { position: absolute; left: 426px; top: 200px; width: 137px; height: 3px; background: var(--blue); }
  .contact { position: absolute; left: 426px; display: flex; align-items: center; gap: 10px; font-size: 27px; color: var(--blue); }
  .contact svg { width: 20px; height: 20px; }
  .contact-phone { top: 236px; }
  .contact-email { top: 276px; }

  .bands { position: absolute; left: 0; top: 0; width: 900px; height: 511px; }
  .band-label { position: absolute; top: 451px; font-size: 26px; color: var(--white); white-space: nowrap; }
  .band-family { left: 61px; }
  .band-licensed { left: 548px; }
</style>
</head>
<body>
  <section class="card card-front">
    <p class="line service-area"><span class="blue">Serves Fernbrook, IA &amp;</span><br><span class="red">Surrounding Areas</span></p>
    <span class="brand-mark front-mark"></span>
    <h1 class="brand-name front-name">DALVICK'S</h1>
    <p class="line tagline red">Air Conditioning &amp; Heating Service</p>
    <p class="line call-out"><span class="blue">Call today for all your </span><span class="red">HVAC</span><span class="blue">,</span><br><span class="red">Refrigeration</span><span class="blue"> &amp; </span><span class="red">Plumbing Needs</span></p>
  </section>

  <section class="card card-back">
    <span class="brand-mark back-mark"></span>
    <p class="brand-name back-name">DALVICK'S</p>

    <h2 class="person-name">MARK DALVICK</h2>
    <span class="divider"></span>
    <p class="contact contact-phone">
      <svg viewBox="0 0 24 24" aria-hidden="true"><path fill="#d4161d" d="M6.6 10.8c1.4 2.8 3.8 5.2 6.6 6.6l2.2-2.2c.3-.3.7-.4 1-.2 1.1.4 2.3.6 3.6.6.6 0 1 .4 1 1V20c0 .6-.4 1-1 1C10.6 21 3 13.4 3 4c0-.6.4-1 1-1h3.5c.6 0 1 .4 1 1 0 1.3.2 2.5.6 3.6.1.3 0 .7-.2 1z"/></svg>
      555.014.2290
    </p>
    <p class="contact contact-email">
      <svg viewBox="0 0 24 24" aria-hidden="true"><path fill="#d4161d" d="M2 5h20v14H2z"/><path fill="none" stroke="#fff" stroke-width="2" d="M2 6l10 7 10-7"/></svg>
      hvacdalvick@mailbox.com
    </p>

    <svg class="bands" viewBox="0 0 900 511" aria-hidden="true">
      <polygon fill="#d4161d" points="0,402 487,432 474,511 0,511"/>
      <polygon fill="#0b6cb3" points="506,432 900,402 900,511 494,511"/>
    </svg>
    <p class="band-label band-family">Family Owned &amp; Operated</p>
    <p class="band-label band-licensed">Licensed &amp; insured</p>
  </section>
</body>
</html>
```